We need a new business card that reflects who we are. Professional, classy, modern, and service ori

We need a business card design for a window coverings design company in Kansas City called Bright Lane Interiors. We offer professional, modern, and high quality window covering products. We are looking to portray an image of a big, national franchise. We are a 5 location (with showrooms) business with 10 professional designers and 4 professional installers. These cards will be used with Thank you cards, given to realtors, and asked for referrals with.

Target Market(s)

Kansas City

Industry/Entity Type

Business

Contact Information for Business Card

We would like our card to look clean and simple on the front, featuring our logo and Marlow Fenwick's. Our designers' phone numbers and emails should be displayed as well as their title.

Font styles to use
Sans Serif

Colors

Designer to choose colors to be used in the design.

Requirements
Must have
• Front - Logos, name, phone number, email address
• Back - Showroom locations, social media? Appt date/time?
Nice to have
• I would like a clean and modern look (not contemporary. I like a white background, but I am open to ideas. Looking for a "National chain" look for a small business.
Should not have
• Too much busyness.

```html
<!DOCTYPE html>
<html lang="en">
<head>
<meta charset="utf-8">
<title>Bright Lane Interiors – Business Card</title>
<link href="https://fonts.googleapis.com/css2?family=Roboto:wght@400;500;700&family=Roboto+Condensed:wght@500;700&display=swap" rel="stylesheet">
<style>
  :root {
    --backdrop: #2a2a2a;
    --card: #f4f4f4;
    --red: #c1393c;
    --ink: #1e1e1e;
    --grey: #555759;
    --soft-grey: #8a8d90;
    --dots: #9a9a9a;
    --accent-orange: #ee8a2a;
  }
  * { margin: 0; padding: 0; box-sizing: border-box; }
  html, body { width: 1200px; height: 960px; overflow: hidden; }
  body {
    background: var(--backdrop);
    font-family: "Roboto", Arial, sans-serif;
    position: relative;
  }
  .card {
    position: absolute;
    left: 320px;
    width: 600px;
    background: var(--card);
    box-shadow: 0 3px 10px rgba(0,0,0,.45);
  }
  .card-back { top: 100px; height: 346px; }
  .card-front { top: 493px; height: 342px; }

  /* Back side */
  .brand-mark {
    position: absolute;
    right: 56px; top: 74px;
    color: var(--ink);
    font-weight: 700;
    font-size: 20px;
  }
  .appt-title {
    position: absolute; left: 45px; top: 95px;
    color: var(--red); font-weight: 500; font-size: 20px;
  }
  .appt-row {
    position: absolute; left: 45px; right: 56px;
    display: flex; align-items: baseline;
    color: var(--red); font-size: 16px;
  }
  .appt-row.name { top: 146px; }
  .appt-row.when { top: 187px; }
  .fill-line {
    flex: 1;
    border-bottom: 1px dotted var(--dots);
    margin: 0 4px;
    transform: translateY(-3px);
  }
  .fill-line.date { flex: none; width: 214px; margin-right: 2px; }
  .ampm { font-size: 12px; margin-left: 2px; }
  .locations {
    position: absolute; left: 45px; top: 240px;
    color: var(--grey); font-weight: 700; font-size: 14.5px;
    white-space: nowrap;
  }
  .social {
    position: absolute; left: 46px; top: 287px;
    display: flex; gap: 5px;
  }
  .social span {
    width: 20px; height: 20px; border-radius: 50%;
    background: var(--red);
  }
  .partner {
    position: absolute; right: 54px; top: 287px;
    display: flex; align-items: center; gap: 5px;
    color: var(--soft-grey); font-weight: 700; font-size: 14px;
  }
  .partner .dot {
    width: 16px; height: 16px; border-radius: 50%;
    background: var(--accent-orange);
  }

  /* Front side */
  .identity {
    position: absolute; left: 40px; top: 180px; width: 250px;
    text-align: center;
  }
  .identity .company {
    color: var(--ink); font-weight: 700; font-size: 24px; line-height: 1.1;
  }
  .identity .tagline {
    margin-top: 8px; color: var(--ink); font-size: 12px;
  }
  .divider {
    position: absolute; left: 304px; top: 110px;
    width: 1px; height: 130px; background: #cfcfcf;
  }
  .person { position: absolute; left: 333px; top: 119px; }
  .person .name {
    font-family: "Roboto Condensed", "Arial Narrow", sans-serif;
    color: var(--red); font-weight: 700; font-size: 24px; line-height: 1;
  }
  .person .title {
    margin-top: 5px; color: var(--ink); font-weight: 500; font-size: 15px;
  }
  .contacts { list-style: none; margin-top: 11px; }
  .contacts li {
    display: flex; align-items: center; gap: 9px;
    color: var(--grey); font-size: 14.5px; line-height: 19px;
  }
  .contacts svg { width: 12px; height: 12px; fill: var(--red); flex: none; }
</style>
</head>
<body>

<section class="card card-back">
  <div class="brand-mark">Bright Lane Interiors</div>
  <h2 class="appt-title">Next Appointment</h2>
  <div class="appt-row name">Name :<span class="fill-line"></span></div>
  <div class="appt-row when">Date :<span class="fill-line date"></span>Time :<span class="fill-line"></span><span class="ampm">AM/PM</span></div>
  <p class="locations">MAPLE RIDGE | CEDAR HOLLOW | PINE CREST | NORTHGATE | WILLOW BEND</p>
  <div class="social" aria-label="Social media"><span></span><span></span><span></span><span></span></div>
  <div class="partner"><span>Marlow Fenwick Gallery</span><span class="dot"></span></div>
</section>

<section class="card card-front">
  <div class="identity">
    <div class="company">Bright Lane Interiors</div>
    <div class="tagline">Window Coverings, Fabrics &amp; Home Styling</div>
  </div>
  <div class="divider"></div>
  <div class="person">
    <div class="name">EVAN CARTER</div>
    <div class="title">DESIGNER</div>
    <ul class="contacts">
      <li><svg viewBox="0 0 24 24"><path d="M6.6 10.8a15.1 15.1 0 0 0 6.6 6.6l2.2-2.2c.3-.3.7-.4 1-.2 1.1.4 2.3.6 3.6.6.6 0 1 .4 1 1V20c0 .6-.4 1-1 1A17 17 0 0 1 3 4c0-.6.4-1 1-1h3.5c.6 0 1 .4 1 1 0 1.3.2 2.5.6 3.6.1.3 0 .7-.2 1z"/></svg>913.555.0148</li>
      <li><svg viewBox="0 0 24 24"><path d="M2 6.5 12 13l10-6.5V19H2z"/><path d="M2 5h20l-10 6.5z"/></svg>info@brightlaneinteriors.com</li>
      <li><svg viewBox="0 0 24 24"><circle cx="12" cy="12" r="10"/><path d="M2 12h20M12 2c3 3 3 17 0 20M12 2c-3 3-3 17 0 20" stroke="#f4f4f4" stroke-width="1.5" fill="none"/></svg>brightlaneinteriors.com</li>
    </ul>
  </div>
</section>

</body>
</html>
```